Stationery for a private security company, "Brenmoor Security Services Ltd."

Needed is a stationery design for a private security company. The designs must show professionalism and that our company mean nothing but business. Watermark of the company logo on the letterhead page is also a must. The final design must represent innovation and professionalism. It would be great if designers could integrate the colours black and silver onto the cards and letterheads..

Thank you

```html
<!DOCTYPE html>
<html lang="en">
<head>
<meta charset="utf-8">
<title>Brenmoor Security Services Ltd. — Stationery</title>
<link href="https://fonts.googleapis.com/css2?family=Open+Sans:wght@400;700&family=Noto+Serif:wght@400&display=swap" rel="stylesheet">
<style>
  :root {
    --backdrop: #4a2e1a;
    --paper: #ffffff;
    --ink: #111111;
    --black-band: #0d0d0d;
    --silver: #b9c3c8;
    --silver-light: #e9ecee;
    --watermark: #ededed;
    --label: #ffffff;
  }
  * { box-sizing: border-box; margin: 0; padding: 0; }
  html, body { width: 1200px; height: 515px; overflow: hidden; }
  body { background: var(--backdrop); font-family: "Open Sans", sans-serif; color: var(--ink); }
  .canvas { position: relative; width: 1200px; height: 515px; }
  .sheet { position: absolute; background: var(--paper); overflow: hidden; box-shadow: 0 2px 6px rgba(0,0,0,.45); }

  .wordmark { font-family: "Open Sans", sans-serif; font-weight: 700; color: var(--ink); text-transform: uppercase; line-height: 1.05; display: flex; align-items: center; gap: 5px; }
  .wordmark .mark { display: inline-block; background: var(--ink); }
  .wordmark span { display: block; }

  .watermark { position: absolute; font-family: "Open Sans", sans-serif; font-weight: 700; color: var(--watermark); text-transform: uppercase; text-align: center; line-height: 1; }

  .footer-rule { position: absolute; left: 0; right: 0; height: 3px; background: var(--silver); }
  .footer-band { position: absolute; left: 0; right: 0; background: var(--black-band); color: #dcdcdc; font-family: "Noto Serif", serif; font-size: 5.6px; text-align: center; }
  .footer-band p { line-height: 1.9; }
  .footer-band .gap { display: inline-block; width: 8px; }

  /* Letterhead */
  .letterhead { left: 26px; top: 25px; width: 342px; height: 431px; }
  .letterhead .wordmark { position: absolute; top: 16px; left: 0; right: 0; justify-content: center; font-size: 12px; }
  .letterhead .wordmark .mark { width: 12px; height: 12px; }
  .letterhead .wordmark small { font-size: 6px; }
  .letterhead .watermark { left: 20px; right: 20px; top: 255px; font-size: 34px; }
  .letterhead .footer-rule { top: 399px; }
  .letterhead .footer-band { top: 405px; height: 26px; padding-top: 3px; }

  /* Fax sheet */
  .fax { left: 385px; top: 28px; width: 343px; height: 432px; }
  .fax .wordmark { position: absolute; top: 16px; left: 15px; font-size: 12px; }
  .fax .wordmark .mark { width: 12px; height: 12px; }
  .fax .wordmark small { font-size: 6px; }
  .fax .address { position: absolute; top: 25px; left: 256px; border-left: 1px solid #666; padding-left: 4px; font-family: "Noto Serif", serif; font-size: 5.6px; line-height: 1.4; }
  .fax .watermark { left: 60px; right: 60px; top: 170px; font-size: 26px; }
  .fax h1 { position: absolute; top: 108px; left: 24px; font-weight: 400; font-size: 19px; }
  .fax-fields { position: absolute; top: 140px; left: 24px; width: 294px; display: grid; grid-template-columns: 175px 1fr; column-gap: 0; row-gap: 0; }
  .fax-fields div { font-size: 5.2px; height: 17.5px; padding-top: 6px; border-bottom: 1px solid #333; }
  .fax-fields div:nth-child(odd) { margin-right: 4px; }
  .fax-checks { position: absolute; top: 228px; left: 24px; width: 294px; display: flex; justify-content: space-between; font-size: 5.2px; }
  .fax-checks span { display: flex; align-items: center; gap: 4px; }
  .fax-checks span::before { content: ""; width: 7px; height: 7px; border: 0.8px solid #333; }
  .fax .footer-rule { top: 404px; }
  .fax .footer-band { top: 410px; height: 22px; padding-top: 6px; }

  /* Envelopes */
  .envelope-back { left: 782px; top: 30px; width: 362px; height: 166px; }
  .envelope-mid { left: 770px; top: 102px; width: 362px; height: 94px; background: var(--silver-light); }
  .envelope-mid .flap-text { position: absolute; left: 0; right: 0; top: 24px; text-align: center; color: #dfe5e8; font-weight: 700; text-transform: uppercase; }
  .envelope-mid .flap-text b { display: block; font-size: 13px; }
  .envelope-mid .flap-text small { font-size: 6px; }
  .envelope-front { left: 744px; top: 186px; width: 384px; height: 166px; }
  .envelope-front .wordmark { position: absolute; top: 12px; left: 11px; font-size: 11px; }
  .envelope-front .wordmark .mark { width: 11px; height: 11px; }
  .envelope-front .wordmark small { font-size: 5.5px; }
  .envelope-front .web { position: absolute; top: 63px; left: 11px; font-family: "Noto Serif", serif; font-size: 5.6px; }
  .envelope-front .watermark { left: 160px; right: 10px; top: 70px; font-size: 24px; }
  .envelope-front .footer-rule { top: 149px; }
  .envelope-front .footer-band { top: 152px; height: 14px; text-align: left; padding: 2px 10px; }

  /* Business cards */
  .card { top: 382px; width: 141px; height: 78px; }
  .card-front { left: 742px; }
  .card-front .wordmark { position: absolute; top: 28px; left: 8px; font-size: 7px; }
  .card-front .wordmark .mark { width: 7px; height: 7px; }
  .card-front .wordmark small { font-size: 3.6px; }
  .card-front .details { position: absolute; top: 18px; left: 70px; border-left: 0.6px solid #777; padding-left: 3px; font-family: "Noto Serif", serif; font-size: 3.2px; line-height: 1.55; }
  .card-front .details li { list-style: none; display: flex; align-items: center; gap: 2px; }
  .card-front .details li::before { content: ""; width: 3px; height: 3px; border-radius: 50%; background: var(--ink); }
  .card-front .details li.plain::before { display: none; }
  .card-front .footer-rule { top: 68px; height: 1.5px; }
  .card-front .footer-band { top: 70px; height: 8px; font-size: 3.2px; padding-top: 1.5px; }
  .card-dark, .card-silver { text-align: center; color: #ffffff; }
  .card-dark { left: 888px; background: var(--black-band); }
  .card-silver { left: 1033px; background: var(--silver); }
  .card .title { position: absolute; left: 0; right: 0; top: 12px; font-weight: 700; text-transform: uppercase; line-height: 1.05; }
  .card .title b { display: block; font-size: 11px; }
  .card .title small { font-size: 5px; }
  .card .site { position: absolute; left: 0; right: 0; top: 61px; font-family: "Noto Serif", serif; font-size: 4px; color: rgba(255,255,255,.55); }

  .option-label { position: absolute; top: 474px; font-size: 21px; color: var(--label); }
</style>
</head>
<body>
<main class="canvas">

  <section class="sheet letterhead" aria-label="Letterhead">
    <div class="wordmark"><i class="mark"></i><span>Brenmoor<br><small>Security Services Ltd.</small></span></div>
    <div class="watermark">Brenmoor</div>
    <div class="footer-rule"></div>
    <footer class="footer-band">
      <p>☏ 123-456-7890<span class="gap"></span>☏ 123-456-7856<span class="gap"></span>✉ brenmoorsecurity@mail.com<span class="gap"></span>● www.brenmoorsecurity.com</p>
      <p>Street Name, City Name State Zipcode</p>
    </footer>
  </section>

  <section class="sheet fax" aria-label="Fax sheet">
    <div class="wordmark"><i class="mark"></i><span>Brenmoor<br><small>Security Services Ltd.</small></span></div>
    <address class="address">Street Name, City Name<br>State Zipcode</address>
    <div class="watermark">Brenmoor</div>
    <h1>FAX</h1>
    <div class="fax-fields">
      <div>To :</div><div>From :</div>
      <div>Fax :</div><div>Pages :</div>
      <div>Phone :</div><div>Date :</div>
      <div>Re :</div><div>CC :</div>
    </div>
    <div class="fax-checks">
      <span>Urgent</span><span>For Review</span><span>Please Comment</span><span>Please Reply</span><span>Please Recycle</span>
    </div>
    <div class="footer-rule"></div>
    <footer class="footer-band">
      <p>☏ 123-456-7890<span class="gap"></span>☏ 123-456-7856<span class="gap"></span>✉ brenmoorsecurity@mail.com<span class="gap"></span>● www.brenmoorsecurity.com</p>
    </footer>
  </section>

  <section class="sheet envelope-back" aria-label="Envelope back">
    <svg width="362" height="166" viewBox="0 0 362 166" aria-hidden="true">
      <path d="M0 0 H362 V22 Q362 30 350 36 L200 70 Q181 74 162 70 L12 36 Q0 30 0 22 Z" fill="#0d0d0d"/>
    </svg>
  </section>

  <section class="sheet envelope-mid" aria-label="Envelope flap">
    <svg width="362" height="94" viewBox="0 0 362 94" style="position:absolute;left:0;top:0" aria-hidden="true">
      <path d="M0 0 H362 V40 L200 72 Q181 76 162 72 L0 40 Z" fill="#b9c3c8"/>
    </svg>
    <div class="flap-text"><b>Brenmoor</b><small>Security Services Ltd.</small></div>
  </section>

  <section class="sheet envelope-front" aria-label="Envelope front">
    <div class="wordmark"><i class="mark"></i><span>Brenmoor<br><small>Security Services Ltd.</small></span></div>
    <p class="web">www.brenmoorsecurity.com</p>
    <div class="watermark">Brenmoor</div>
    <div class="footer-rule"></div>
    <footer class="footer-band"><p>Street Name, City Name State Zipcode</p></footer>
  </section>

  <section class="sheet card card-front" aria-label="Business card front">
    <div class="wordmark"><i class="mark"></i><span>Brenmoor<br><small>Security Services Ltd.</small></span></div>
    <ul class="details">
      <li class="plain">Street Name, City Name</li>
      <li class="plain">State Zipcode</li>
      <li>123-456-7890</li>
      <li>123-456-7856</li>
      <li>brenmoorsecurity@mail.com</li>
      <li>www.brenmoorsecurity.com</li>
    </ul>
    <div class="footer-rule"></div>
    <footer class="footer-band"><p>Your Name, Designation</p></footer>
  </section>

  <section class="sheet card card-dark" aria-label="Business card back, black">
    <div class="title"><b>Brenmoor</b><small>Security Services Ltd.</small></div>
    <p class="site">www.brenmoorsecurity.com</p>
  </section>

  <section class="sheet card card-silver" aria-label="Business card back, silver">
    <div class="title"><b>Brenmoor</b><small>Security Services Ltd.</small></div>
    <p class="site">www.brenmoorsecurity.com</p>
  </section>

  <p class="option-label" style="left:148px">Option-1</p>
  <p class="option-label" style="left:512px">Option-2</p>

</main>
</body>
</html>
```